Brightway Haus Inc. Business Card Design

Brightway Haus Inc. is in search of a great clean design for our business cards!

Looking to incorporate our full logo and watermark on side one (however, I am open to having the text and watermark separated within the design.)

On side two, I am looking to have contact information (Name, Position, Phone #, Email, Website (www.thebrightwayhaus.ca). Can have the logo and/or watermark as part of the design if applicable.

Please add tagline "Where Shine Counts" on either side 1 or 2. This tagline can be in a sans serif, serif or cursive font as long as it compliments overall design. Capitalization can be title or sentence case depending on how it fits within the design.

Get creative!! Looking for a clean, crisp, premium design! Looking for a glossy card finish with spot UV features when printed. Cards will also be printed with rounded corners. Standard dimensions (3.5 x 2).

Target Market(s)

B2B - primary clients are business owners or property management corporations. (residential jobs are few and far between)

Industry/Entity Type

Business

Contact Information for Business Card

- clean, crisp design
- double sided
- spot UV accents and glossy finish upon printing
- standard business card size (3.5 x 2) with rounded corners
- please see project description for requirements per side

Font styles to use
Sans Serif

Requirements
Must have
• - adequate bleeds with print ready files
• - cohesive design elements between side 1 & 2
• - spot UV elements (can be on both sides or just one, use your discretion)
• - colour pallet should match the logo file provided
• - incorporate tagline "where shine counts" (this tagline can be in a serif or sans serif font as long as it is complimentary to the overall design.
Nice to have
• - Premium elements with a clean design
Should not have
• - Please omit cartoon or whimsical like designs, think premium.
• - Colours should not stray from the pallet of the provided logo.

```html
<!DOCTYPE html>
<html lang="en">
<head>
<meta charset="utf-8">
<title>Brightway Haus Inc. Business Card</title>
<link rel="stylesheet" href="https://fonts.googleapis.com/css2?family=Open+Sans:wght@700;800&family=Roboto:wght@400;500;700&display=swap">
<style>
  :root {
    --teal: #139c9e;
    --teal-dark: #0f8d90;
    --navy: #1c1d45;
    --ink: #262844;
    --paper: #efefef;
    --card-light: #f1f1f1;
    --card-light-2: #e3e3e3;
    --white: #ffffff;
    --bg: #e6e6e6;
  }
  * { margin: 0; padding: 0; box-sizing: border-box; }
  html, body {
    width: 1200px; height: 576px; overflow: hidden;
    background: var(--bg);
    font-family: "Roboto", Arial, sans-serif;
  }
  .sheet { position: relative; width: 1200px; height: 576px; }
  .card {
    position: absolute; top: 138px;
    width: 484px; height: 294px;
    border-radius: 11px; overflow: hidden;
    box-shadow: 0 3px 8px rgba(0,0,0,.18);
  }
  .card--front {
    left: 82px;
    background: linear-gradient(160deg, var(--teal) 0%, var(--teal-dark) 100%);
  }
  .card--back {
    left: 602px; width: 481px;
    background: linear-gradient(135deg, var(--card-light) 0%, var(--card-light-2) 100%);
  }
  .front-name {
    position: absolute; left: 0; right: 0; top: 124px;
    text-align: center;
    font-family: "Open Sans", Arial, sans-serif;
    font-weight: 800; font-size: 34px; letter-spacing: -0.5px;
    color: var(--white);
  }
  .back-brand {
    position: absolute; left: 0; width: 270px; top: 108px;
    display: flex; flex-direction: column; align-items: center;
  }
  .brand-square {
    width: 44px; height: 44px; background: var(--teal); margin-bottom: 14px;
  }
  .back-name {
    font-family: "Open Sans", Arial, sans-serif;
    font-weight: 800; font-size: 21px; letter-spacing: -0.3px;
    color: var(--teal); white-space: nowrap;
  }
  .contact {
    position: absolute; left: 282px; top: 66px; color: var(--ink);
  }
  .contact__name { font-size: 21px; font-weight: 700; color: var(--teal); line-height: 1.1; }
  .contact__role { font-size: 11.5px; margin-top: 5px; }
  .contact__address { font-size: 12px; line-height: 17px; margin-top: 20px; }
  .contact__list { list-style: none; margin-top: 2px; }
  .contact__list li {
    display: flex; align-items: center; gap: 9px;
    font-size: 12px; line-height: 18px;
  }
  .contact__list svg { width: 10px; height: 10px; fill: var(--teal); flex: none; }
  .accent { color: var(--teal); }
  .band { position: absolute; left: 0; bottom: 0; width: 481px; height: 40px; }
  .tagline {
    position: absolute; left: 282px; bottom: 10px;
    font-size: 11px; letter-spacing: 0.6px; color: var(--white);
  }
</style>
</head>
<body>
<main class="sheet">
  <section class="card card--front" aria-label="Card front">
    <div class="front-name">BRIGHTWAY HAUS INC.</div>
  </section>

  <section class="card card--back" aria-label="Card back">
    <div class="back-brand">
      <div class="brand-square"></div>
      <div class="back-name">BRIGHTWAY HAUS INC.</div>
    </div>

    <div class="contact">
      <div class="contact__name">Daniel Reyes</div>
      <div class="contact__role">Managing Director</div>
      <div class="contact__address">48, Harbour Lane Street<br>Suite 9, Canada 410</div>
      <ul class="contact__list">
        <li>
          <svg viewBox="0 0 10 10" aria-hidden="true"><path d="M1 3.5C1 2 2.5 1 5 1s4 1 4 2.5L7.5 4 7 3H3l-.5 1zM2.5 5h5l1 4h-7z"/></svg>
          1800-555-0142
        </li>
        <li>
          <svg viewBox="0 0 10 10" aria-hidden="true"><path d="M0 2h10v6H0zM1 3v.3l4 2.5 4-2.5V3L5 5.3z"/></svg>
          danielreyes@brightway.ca
        </li>
        <li>
          <svg viewBox="0 0 10 10" aria-hidden="true"><circle cx="5" cy="5" r="4.5"/><path d="M.5 5h9M5 .5v9" stroke="#fff" stroke-width=".7"/></svg>
          <span>www.<span class="accent">thebrightwayhaus</span>.ca</span>
        </li>
      </ul>
    </div>

    <svg class="band" viewBox="0 0 481 40" aria-hidden="true">
      <rect x="0" y="24" width="470" height="16" fill="var(--navy)"/>
      <polygon points="258,6 481,6 481,40 244,40" fill="var(--teal)"/>
    </svg>
    <div class="tagline">Where Shine Counts</div>
  </section>
</main>
</body>
</html>
```